KBT Business Cards

We require business cards for our business. We would like a matte black back to the card, with our logo centred in the middle. The front side of the card is open to design.

Target Market(s)

Clients looking for legal services (professional)

Industry/Entity Type

Legal

Contact Information for Business Card

Doran Kelbrath
Partner
Mobile: 0461 738 524
Email: doran@kbtlaw.co
Website: www.kbtlaw.co
Level 3, 118 Wendmore Street
Sydney NSW 2000

Font styles to use
Other font styles liked:
• Avenir

Colors
f04a50
ffffff
1b1b1b

Requirements
Must have
• Black back with logo included in the centre of the card.
• Our font is Avenir.

```html
<!DOCTYPE html>
<html lang="en">
<head>
<meta charset="utf-8">
<title>Kelbrath Brenner Legal – Business Cards</title>
<link rel="stylesheet" href="https://fonts.googleapis.com/css2?family=Nunito+Sans:wght@400;600;800&display=swap">
<style>
  :root {
    --red: #f04a50;
    --red-deep: #c8193f;
    --white: #ffffff;
    --ink: #1b1b1b;
    --stage: #2b2b2b;
    --muted: #3a3a3a;
  }
  * { margin: 0; padding: 0; box-sizing: border-box; }
  html, body {
    width: 1200px; height: 960px; overflow: hidden;
    background: var(--stage);
    font-family: "Nunito Sans", "Avenir", sans-serif;
  }
  .card {
    position: absolute; left: 250px;
    width: 700px; height: 400px;
    overflow: hidden;
    box-shadow: 0 12px 30px rgba(0,0,0,.35);
  }
  /* Back */
  .card--back { top: 60px; background: var(--ink); }
  .brand {
    position: absolute; display: flex; align-items: center; gap: 22px;
  }
  .brand__mark { width: 70px; height: 70px; background: var(--red-deep); flex: none; }
  .brand__name {
    font-weight: 800; font-size: 34px; line-height: 1.0;
    text-transform: uppercase; letter-spacing: .5px;
  }
  .card--back .brand { left: 50%; top: 140px; transform: translateX(-50%); }
  .card--back .brand__name { color: var(--white); }
  .back__web {
    position: absolute; left: 0; right: 0; top: 300px; text-align: center;
    color: var(--white); font-size: 15px; letter-spacing: 4px;
  }
  .back__web .accent { color: var(--red); font-weight: 800; }

  /* Front */
  .card--front { top: 500px; background: var(--white); color: var(--ink); }
  .card--front .brand { left: 380px; top: 70px; }
  .card--front .brand__mark { width: 62px; height: 62px; }
  .card--front .brand__name { color: var(--ink); font-size: 30px; }
  .person { position: absolute; left: 60px; top: 60px; }
  .person__name {
    color: var(--red-deep); font-weight: 800; font-size: 22px; letter-spacing: .3px;
  }
  .person__role { font-size: 15px; letter-spacing: 1px; margin-top: 2px; }
  .contact { position: absolute; left: 60px; top: 186px; list-style: none; font-size: 15px; }
  .contact li { display: flex; align-items: center; gap: 10px; margin-bottom: 8px; }
  .contact svg { width: 14px; height: 14px; flex: none; }
  .address {
    position: absolute; right: 40px; top: 264px; text-align: right;
    font-size: 16px; line-height: 1.4;
  }
  .front__web {
    position: absolute; right: 40px; bottom: 12px;
    color: var(--white); font-size: 16px; letter-spacing: 3.5px;
  }
  .decor { position: absolute; inset: 0; }
</style>
</head>
<body>

<section class="card card--back" aria-label="Card back">
  <div class="brand">
    <span class="brand__mark"></span>
    <span class="brand__name">Kelbrath<br>Brenner<br>Legal</span>
  </div>
  <p class="back__web">www.<span class="accent">kbtlaw</span>.co</p>
</section>

<section class="card card--front" aria-label="Card front">
  <svg class="decor" viewBox="0 0 700 400" aria-hidden="true">
    <rect x="60" y="165" width="60" height="3" fill="var(--ink)"/>
    <line x1="120" y1="166.5" x2="700" y2="258" stroke="var(--ink)" stroke-width="1.5"/>
    <polygon points="0,318 340,318 356,334 0,334" fill="var(--red-deep)"/>
    <polygon points="0,340 352,340 374,362 700,362 700,400 0,400" fill="var(--ink)"/>
  </svg>

  <div class="person">
    <p class="person__name">DORAN KELBRATH</p>
    <p class="person__role">PARTNER</p>
  </div>

  <ul class="contact">
    <li>
      <svg viewBox="0 0 14 14"><rect width="14" height="14" rx="2" fill="var(--red-deep)"/><rect x="4.5" y="2.5" width="5" height="9" rx="1" fill="none" stroke="var(--white)" stroke-width="1"/></svg>
      0461 738 524
    </li>
    <li>
      <svg viewBox="0 0 14 14"><rect width="14" height="14" rx="2" fill="var(--red-deep)"/><rect x="2.5" y="4" width="9" height="6" fill="none" stroke="var(--white)" stroke-width="1"/><polyline points="2.5,4 7,7.5 11.5,4" fill="none" stroke="var(--white)" stroke-width="1"/></svg>
      doran@kbtlaw.co
    </li>
  </ul>

  <div class="brand">
    <span class="brand__mark"></span>
    <span class="brand__name">Kelbrath<br>Brenner<br>Legal</span>
  </div>

  <address class="address" style="font-style:normal">
    Level 3, 118 Wendmore Street<br>Sydney NSW 2000
  </address>

  <p class="front__web">www.kbtlaw.co</p>
</section>

</body>
</html>
```